Upscale business cards needed for Board of Directors

We need professional business cards created for members of our family business Board of Directors. We would like these relatively simple and straightforward, but also with a unique element to set them apart. Probably stick with neutral and simple colors - white, grey etc. We need space for the traditional elements, including name, title, address, email/phone number. And we will be creating several from this template so it needs to be template that is easy to switch information in and out of.
Business
See description

```html
<!DOCTYPE html>
<html lang="en">
<head>
<meta charset="utf-8">
<title>Harbourline Holdings – Business Card</title>
<link rel="stylesheet" href="https://fonts.googleapis.com/css2?family=Open+Sans:wght@400;600&display=swap">
<style>
  :root {
    --page-bg: #e6e4e1;
    --panel-dark: #1c1c1d;
    --panel-dark-edge: #2b2b2c;
    --frost-light: #f1f1ef;
    --frost-mid: #dcdcda;
    --gold: #a8875a;
    --gold-deep: #7d6140;
    --ink: #141414;
    --text-light: #e4e4e4;
  }
  * { margin: 0; padding: 0; box-sizing: border-box; }
  html, body {
    width: 1200px;
    height: 969px;
    overflow: hidden;
    background: var(--page-bg);
    font-family: "Open Sans", Arial, sans-serif;
  }
  .business-card {
    position: absolute;
    left: 150px;
    top: 229px;
    width: 900px;
    height: 510px;
    background: linear-gradient(160deg, var(--frost-light) 0%, var(--frost-mid) 100%);
    box-shadow: 0 18px 40px rgba(0,0,0,0.18);
    overflow: hidden;
  }
  .contact-panel {
    position: absolute;
    left: 0; top: 0;
    width: 373px;
    height: 100%;
    background: linear-gradient(180deg, var(--panel-dark-edge) 0%, var(--panel-dark) 60%, #111 100%);
    color: var(--text-light);
    padding-left: 46px;
  }
  .holder-name {
    position: absolute;
    top: 100px;
    font-size: 28px;
    font-weight: 400;
    letter-spacing: 1px;
    color: var(--gold);
  }
  .holder-title {
    position: absolute;
    top: 140px;
    font-size: 23px;
  }
  .address {
    position: absolute;
    top: 224px;
    font-size: 22px;
    line-height: 34px;
  }
  .contact-list {
    position: absolute;
    top: 302px;
    list-style: none;
    font-size: 22px;
    line-height: 35px;
  }
  .contact-list li { display: flex; align-items: center; }
  .contact-icon { width: 22px; height: 22px; margin-right: 22px; fill: var(--gold); }
  .brand-name {
    position: absolute;
    left: 373px;
    top: 232px;
    width: 495px;
    text-align: center;
    color: var(--ink);
    font-size: 34px;
    font-weight: 600;
    line-height: 1.2;
  }
  .edge-strip {
    position: absolute;
    right: 10px;
    top: 0;
    width: 12px;
    height: 100%;
    background: linear-gradient(180deg, var(--gold) 0%, var(--gold-deep) 100%);
  }
</style>
</head>
<body>
  <div class="business-card">
    <div class="contact-panel">
      <p class="holder-name">DANIEL REYES</p>
      <p class="holder-title">President</p>
      <p class="address">4127 Larchmont Avenue<br>Glen Haven, NY 11024</p>
      <ul class="contact-list">
        <li>
          <svg class="contact-icon" viewBox="0 0 24 24" aria-hidden="true"><path d="M3 7c0-2 4-4 9-4s9 2 9 4v2h-5V7H8v2H3z M6 11h12l2 9H4z"/></svg>
          555 0142 7786
        </li>
        <li>
          <svg class="contact-icon" viewBox="0 0 24 24" aria-hidden="true"><path d="M2 5h20v2l-10 6L2 7z M2 9l10 6 10-6v10H2z"/></svg>
          daniel@harbourline.co
        </li>
        <li>
          <svg class="contact-icon" viewBox="0 0 24 24" aria-hidden="true"><circle cx="12" cy="12" r="10"/><path d="M2 12h20M12 2c3 3 3 17 0 20M12 2c-3 3-3 17 0 20" stroke="#1c1c1d" stroke-width="1.6" fill="none"/></svg>
          www.harbourline.co
        </li>
      </ul>
    </div>
    <p class="brand-name">Harbourline Holdings</p>
    <div class="edge-strip"></div>
  </div>
</body>
</html>
```